Tech business card design

We need an amazing business card design for our new business 'Pexla' a marketing tech startup based in Sydney, Australia. We provide an online marketplace for businesses to search and buy advertising media, connect with service providers and learn more about marketing. We wish to communicate 'cool tech', reliability and professionalism and design based around our logo.

Target Market(s)

Business Owners

Contact Information for Business Card

Name
Position
Email Address
Website
Phone Number

Font styles to use
Other font styles liked:
• Avenir & Avenir Next

Colors

Designer to choose colors to be used in the design.

```html
<!DOCTYPE html>
<html lang="en">
<head>
<meta charset="utf-8">
<title>Pexla Business Card</title>
<link rel="stylesheet" href="https://fonts.googleapis.com/css2?family=Montserrat:wght@600;700&family=Open+Sans:wght@400&display=swap">
<style>
  :root {
    --backdrop: #2a2a2c;
    --card: #1f1f21;
    --card-edge: #161617;
    --ink: #f2f2f4;
    --ink-soft: #d6d6da;
    --rule: #8a8a90;
    --pattern-top: #2b2b2e;
    --pattern-bottom: #1f1f21;
  }
  * { margin: 0; padding: 0; box-sizing: border-box; }
  html, body { width: 1200px; height: 1108px; overflow: hidden; }
  body {
    background: var(--backdrop);
    font-family: "Open Sans", Arial, sans-serif;
    position: relative;
  }
  .card {
    position: absolute;
    top: 214px;
    width: 420px;
    height: 680px;
    background: var(--card);
    border-radius: 30px;
    box-shadow: 0 18px 40px rgba(0,0,0,0.45);
    overflow: hidden;
    color: var(--ink);
  }
  .card--front { left: 150px; }
  .card--back { left: 630px; }

  .wordmark {
    position: absolute;
    font-family: "Montserrat", Arial, sans-serif;
    font-weight: 700;
    color: var(--ink);
    letter-spacing: -2px;
    line-height: 1;
  }
  .card--front .wordmark { top: 150px; left: 0; width: 100%; text-align: center; font-size: 104px; }
  .card--back .wordmark { bottom: 98px; left: 0; width: 100%; text-align: center; font-size: 104px; }

  .identity {
    position: absolute;
    top: 420px;
    left: 0;
    width: 100%;
    text-align: center;
  }
  .identity__name {
    font-family: "Montserrat", Arial, sans-serif;
    font-weight: 600;
    font-size: 25px;
    letter-spacing: 1px;
  }
  .identity__role {
    font-size: 17px;
    color: var(--ink-soft);
    margin-top: 2px;
  }
  .divider {
    display: flex;
    align-items: center;
    justify-content: center;
    gap: 8px;
    margin: 10px auto 8px;
    width: 300px;
  }
  .divider__line { flex: 1; height: 1px; background: var(--rule); }
  .divider svg { width: 20px; height: 20px; }
  .contacts { list-style: none; font-size: 18px; line-height: 1.45; color: var(--ink); }

  .pattern-field {
    position: absolute;
    inset: 0 0 200px 0;
    background: linear-gradient(160deg, var(--pattern-top), var(--pattern-bottom));
  }
</style>
</head>
<body>
  <section class="card card--front">
    <div class="wordmark">pexla</div>
    <div class="identity">
      <p class="identity__name">MARCUS HALE</p>
      <p class="identity__role">Managing Director</p>
      <div class="divider">
        <span class="divider__line"></span>
        <svg viewBox="0 0 20 20" aria-label="phone"><circle cx="10" cy="10" r="9.5" fill="#f2f2f4"/><path d="M6.5 5.5l2 0 .8 2.4-1.2.9a6 6 0 0 0 3.1 3.1l.9-1.2 2.4.8v2c0 .6-.5 1-1 1A8.5 8.5 0 0 1 5.5 6.5c0-.5.4-1 1-1z" fill="#1f1f21"/></svg>
        <svg viewBox="0 0 20 20" aria-label="email"><circle cx="10" cy="10" r="9.5" fill="#f2f2f4"/><rect x="5" y="6.5" width="10" height="7" fill="none" stroke="#1f1f21" stroke-width="1.3"/><path d="M5 6.5l5 4 5-4" fill="none" stroke="#1f1f21" stroke-width="1.3"/></svg>
        <svg viewBox="0 0 20 20" aria-label="website"><circle cx="10" cy="10" r="9.5" fill="#f2f2f4"/><circle cx="10" cy="10" r="5" fill="none" stroke="#1f1f21" stroke-width="1.3"/><path d="M5 10h10M10 5c-2.5 3-2.5 7 0 10M10 5c2.5 3 2.5 7 0 10" fill="none" stroke="#1f1f21" stroke-width="1.1"/></svg>
        <span class="divider__line"></span>
      </div>
      <ul class="contacts">
        <li>044-987 654 321</li>
        <li>info@pexlamail.com</li>
        <li>www.pexlasite.com</li>
      </ul>
    </div>
  </section>

  <section class="card card--back">
    <div class="pattern-field" role="img" aria-label="Faint repeated brand-name pattern across the back of the card"></div>
    <div class="wordmark">pexla</div>
  </section>
</body>
</html>
```